Change of trading name, rebrand

existing website to be updated with new theme and logo. existing website is
www.harlowbrentmere.com.au
Industry/Entity Type
Construction
Coding
Coded - Design and coding required
Number of Pages Required
5+ page
Requirements
Must have
- be mobile phone friendly

```html
<!DOCTYPE html>
<html lang="en">
<head>
<meta charset="utf-8">
<meta name="viewport" content="width=device-width, initial-scale=1">
<title>HBR Plant Hire</title>
<link href="https://fonts.googleapis.com/css2?family=Oswald:wght@500;600;700&family=Poppins:wght@400;500;600;700&display=swap" rel="stylesheet">
<style>
:root{
  --navy:#1f2577;
  --navy-dark:#141957;
  --ink:#0c0d12;
  --black:#08090c;
  --white:#ffffff;
  --grey:#eeeeee;
  --text:#555a66;
  --muted:#b9bccb;
  --steel:#6f7480;
  --machine:#d9a21c;
}
*{box-sizing:border-box;margin:0;padding:0}
html,body{width:1200px;height:5338px;overflow:hidden}
body{font-family:"Poppins",sans-serif;color:var(--text);background:var(--white);font-size:15px}
h1,h2,h3,.display{font-family:"Oswald",sans-serif;text-transform:uppercase}
a{color:inherit;text-decoration:none}
.wrap{width:1040px;margin:0 auto;position:relative}
.btn{display:inline-flex;align-items:center;gap:10px;background:var(--navy);color:var(--white);font-weight:600;font-size:14px;padding:12px 24px}
.btn svg{width:16px;height:10px}

/* top bar */
.topbar{height:36px;background:var(--navy-dark);color:var(--white);font-size:13px}
.topbar .wrap{display:flex;justify-content:space-between;align-items:center;height:36px}
.social{display:flex;gap:8px}
.social span{width:18px;height:18px;border:1px solid #fff;display:block}
.contacts{display:flex;gap:26px;align-items:center}
.contacts span{display:flex;align-items:center;gap:6px}

/* header */
.header{height:114px;background:var(--white);border-bottom:1px solid #ddd}
.header .wrap{display:flex;align-items:center;justify-content:space-between;height:114px}
.brand{display:flex;align-items:center;gap:10px;font-family:"Oswald",sans-serif;font-weight:700;font-size:30px;color:var(--navy)}
.brand i{width:22px;height:22px;background:var(--navy);display:block}
.nav{display:flex;gap:34px;align-items:center;font-weight:500;font-size:15px;color:#1b1b25}
.nav .btn{padding:11px 22px}

/* hero */
.hero{height:510px;position:relative;background:linear-gradient(100deg,#3b3f47,#23262c 60%,#15171b)}
.hero .content{position:absolute;right:80px;top:110px;color:var(--white);width:560px}
.hero .kicker{font-family:"Oswald";letter-spacing:2px;font-size:17px;font-weight:500}
.hero h1{font-size:46px;line-height:1.1}
.hero h1 strong{display:block;font-size:104px;line-height:1}
.hero p{font-size:17px;margin:6px 0 20px}
.hero .arrows{position:absolute;right:80px;bottom:34px;display:flex;gap:16px}

/* about */
.about{height:610px;padding-top:150px}
.about .wrap{display:flex;justify-content:space-between}
.about .copy{width:470px}
.eyebrow{font-family:"Oswald";font-weight:600;font-size:14px;color:var(--navy);letter-spacing:1px}
.about h2{font-size:42px;color:var(--navy);margin:8px 0 4px}
.about .tag{font-weight:600;color:#222;font-size:14px;margin-bottom:16px}
.about p{font-size:15px;line-height:1.6;margin-bottom:28px}
.about .photo{width:480px;height:330px;background:linear-gradient(160deg,#9fc2e4,#d8dfe6 55%,#b89350);}

/* plant hire */
.plant{height:1270px;background:var(--ink);color:var(--white);padding-top:90px;text-align:center}
.plant .eyebrow{color:var(--white)}
.plant h2{font-size:44px;line-height:1.1;margin-top:6px}
.plant .sub{font-weight:600;font-size:16px;margin:10px 0 44px}
.grid3{display:grid;grid-template-columns:repeat(3,330px);gap:50px 25px;text-align:left}
.card .pic{height:224px;margin-bottom:18px}
.card h3{font-family:"Poppins";text-transform:none;font-size:19px;font-weight:600;line-height:1.25}
.card p{color:var(--muted);font-size:14px;line-height:1.5;margin:8px 0 14px;height:42px;overflow:hidden}
.card a{font-weight:600;font-size:14px;display:flex;gap:8px;align-items:center}
.plant .btn{margin-top:42px}

/* why */
.why{height:570px;padding-top:55px}
.why .wrap{display:flex}
.why .visual{width:460px;height:470px;position:relative}
.why .frame{position:absolute;left:70px;top:20px;width:300px;height:440px;border:12px solid var(--navy)}
.why .pic{position:absolute;left:0;top:90px;width:400px;height:300px;background:radial-gradient(ellipse at center,#e7b23a,#c58f1a 45%,rgba(255,255,255,0) 72%)}
.why h2{font-size:44px;color:#111;margin:30px 0 40px}
.stats{display:grid;grid-template-columns:260px 280px;gap:34px 20px}
.stat{display:flex;align-items:center;gap:14px;color:var(--navy)}
.stat svg{width:56px;height:56px}
.stat b{font-family:"Oswald";font-style:italic;font-size:50px;line-height:1;display:block}
.stat small{font-weight:600;font-size:14px;color:#222}
.stat.wide{grid-column:1/3}

/* projects */
.projects{height:770px;background:var(--black);color:var(--white);padding-top:100px}
.projects .head{display:flex;align-items:flex-start;gap:60px;margin-bottom:40px}
.projects h2{font-size:42px;width:260px}
.projects .head p{width:480px;font-size:15px;line-height:1.55;color:var(--muted)}
.projects .head .btn{margin-left:auto}
.pgrid{display:grid;grid-template-columns:repeat(3,1fr);gap:14px}
.proj{height:245px;position:relative}
.proj .cap{position:absolute;left:0;right:0;bottom:0;padding:16px 18px;background:linear-gradient(transparent,rgba(0,0,0,.85))}
.proj small{font-size:11px;color:#ddd;display:block}
.proj b{font-size:17px;font-weight:600;display:block;line-height:1.25}

/* contact */
.contact{height:660px;padding-top:100px}
.contact .wrap{display:flex;justify-content:space-between}
.form{width:420px;height:470px;background:var(--navy);padding:36px 34px;color:var(--white)}
.form h2{font-size:32px;line-height:1.15;margin-bottom:22px}
.form label{display:block;background:var(--white);color:#777;font-size:13px;padding:10px 12px;margin-bottom:10px}
.form .area{height:86px}
.form .btn{background:var(--navy-dark);border:1px solid #fff;float:right;margin-top:6px}
.contact .visual{width:520px;height:470px;position:relative}
.contact .frame{position:absolute;left:150px;top:20px;width:290px;height:430px;border:12px solid var(--navy)}
.contact .pic{position:absolute;left:10px;top:0;width:430px;height:420px;background:radial-gradient(ellipse at center,#e2ad2f,#c38e1b 40%,rgba(255,255,255,0) 70%)}

/* partners */
.partners{height:290px;background:var(--grey);padding-top:50px;text-align:center}
.partners h2{font-size:38px;color:#111;letter-spacing:2px;margin-bottom:40px}
.logos{display:flex;align-items:center;justify-content:center;gap:34px}
.logos span{display:block;width:110px;height:44px;background:#c9cbd1;border-radius:4px}
.logos .chev{color:#555;font-size:26px}

/* footer */
.footer{height:508px;background:var(--black);color:var(--white);padding-top:95px}
.cols{display:grid;grid-template-columns:260px 260px 260px 260px}
.cols h4{font-family:"Oswald";font-size:16px;letter-spacing:1px;margin-bottom:22px}
.cols p,.cols li{font-size:14px;line-height:1.75;color:#d0d2da;list-style:none}
.cols .phone{font-family:"Oswald";font-size:26px;color:var(--white)}
.legal{position:absolute;left:0;right:0;top:5258px;border-top:1px solid #2a2b33;height:80px}
.legal .wrap{display:flex;justify-content:space-between;align-items:center;height:80px;font-size:13px;color:#aaa}
</style>
</head>
<body>

<div class="topbar"><div class="wrap">
  <div class="social"><span></span><span></span></div>
  <div class="contacts">
    <span><svg width="12" height="14" viewBox="0 0 12 14"><path d="M6 0a5 5 0 0 0-5 5c0 4 5 9 5 9s5-5 5-9a5 5 0 0 0-5-5zm0 7a2 2 0 1 1 0-4 2 2 0 0 1 0 4z" fill="#fff"/></svg>18 Wattle Ridge Rd, Coomera QLD 4209</span>
    <span><svg width="13" height="13" viewBox="0 0 24 24"><path d="M6.6 10.8a15 15 0 0 0 6.6 6.6l2.2-2.2c.3-.3.7-.4 1-.2 1.1.4 2.3.6 3.6.6.6 0 1 .4 1 1V20c0 .6-.4 1-1 1A17 17 0 0 1 3 4c0-.6.4-1 1-1h3.5c.6 0 1 .4 1 1 0 1.3.2 2.5.6 3.6.1.3 0 .7-.2 1z" fill="#fff"/></svg>1300 462 915</span>
  </div>
</div></div>

<header class="header"><div class="wrap">
  <a class="brand" href="#"><i></i>HBR Plant Hire</a>
  <nav class="nav">
    <a href="#">Home</a><a href="#">About us</a><a href="#">Plant Hire</a><a href="#">Major Project Snapshot</a><a href="#">Policies</a><a href="#">Jobs</a>
    <a class="btn" href="#">Contact us <svg viewBox="0 0 16 10"><path d="M0 5h14M10 1l4 4-4 4" stroke="#fff" stroke-width="1.6" fill="none"/></svg></a>
  </nav>
</div></header>

<section class="hero" role="img" aria-label="Excavator working on a construction site at dusk">
  <div class="content">
    <div class="kicker">SPECIALISE IN THE HIRE OF HEAVY EARTHMOVING,</div>
    <h1>Mining and Construction<strong>Machines</strong></h1>
    <p>With specialised attachments and tooling</p>
    <a class="btn" href="#">Learn More <svg viewBox="0 0 16 10"><path d="M0 5h14M10 1l4 4-4 4" stroke="#fff" stroke-width="1.6" fill="none"/></svg></a>
  </div>
  <div class="arrows">
    <svg width="44" height="12" viewBox="0 0 44 12"><path d="M44 6H2M7 1 2 6l5 5" stroke="#fff" stroke-width="1.6" fill="none"/></svg>
    <svg width="44" height="12" viewBox="0 0 44 12"><path d="M0 6h42M37 1l5 5-5 5" stroke="#fff" stroke-width="1.6" fill="none"/></svg>
  </div>
</section>

<section class="about"><div class="wrap">
  <div class="copy">
    <div class="eyebrow">ABOUT US</div>
    <h2>HBR Heavy Equipment Hire</h2>
    <div class="tag">Committed to superior quality plant hire services</div>
    <p>Harlow Brentmere Heavy Equipment Hire specialise in the hire of heavy earthmoving, mining and construction machines with specialised attachments and tooling. Our array of machines and attachments is second to none, and we have one of the largest hire fleets available in South East Queensland.</p>
    <a class="btn" href="#">Read More <svg viewBox="0 0 16 10"><path d="M0 5h14M10 1l4 4-4 4" stroke="#fff" stroke-width="1.6" fill="none"/></svg></a>
  </div>
  <div class="photo" role="img" aria-label="Yellow excavator on an open site under a blue sky"></div>
</div></section>

<section class="plant"><div class="wrap">
  <div class="eyebrow">PLANT HIRE</div>
  <h2>Reliable Plant Hire Spanning<br>Queensland &amp; Surrounds</h2>
  <div class="sub">We Have One of the Largest &amp; Most Versatile Fleets in South East Queensland.</div>
  <div class="grid3">
    <article class="card"><div class="pic" role="img" aria-label="Orange excavator on a dirt site" style="background:linear-gradient(160deg,#b6c6d6,#8a6a4c 60%,#c4592a)"></div><h3>Excavators &amp; diggers for hire</h3><p>We are proud of our broad range of excavators fitted with state-of-the-art GPS, spanning reliable and trusted models.</p><a href="#">Read More →</a></article>
    <article class="card"><div class="pic" role="img" aria-label="Yellow dozer on a gravel pad" style="background:linear-gradient(160deg,#c3cbd2,#cfa43c 55%,#7b6b55)"></div><h3>Dozers for hire</h3><p>The most prolific brands of dozer manufacturers are major dozer makers and leading brands – and we have both machine types.</p><a href="#">Read More →</a></article>
    <article class="card"><div class="pic" role="img" aria-label="Swamp dozer working on soft ground" style="background:linear-gradient(160deg,#a9bdcf,#d6b041 55%,#6f6250)"></div><h3>Swamp dozers for hire</h3><p>The most prolific brands of dozer manufacturers are major dozer makers and leading brands – and we have both.</p><a href="#">Read More →</a></article>
    <article class="card"><div class="pic" role="img" aria-label="Articulated dump truck on a haul road" style="background:linear-gradient(160deg,#9fb4c8,#d8b84a 50%,#5f5a52)"></div><h3>Articulated, tracked &amp; rigid dump trucks for hire</h3><p>Our new and well-maintained fleet of articulated dump trucks for hire ranging in size.</p><a href="#">Read More →</a></article>
    <article class="card"><div class="pic" role="img" aria-label="Grader parked on a worksite" style="background:linear-gradient(160deg,#d2d5d4,#b79a62 55%,#6d5a45)"></div><h3>Graders for hire</h3><p>We own and operate a fleet of premium brand graders for hire, a number of graders and more.</p><a href="#">Read More →</a></article>
    <article class="card"><div class="pic" role="img" aria-label="Stacked pipes and loader on site" style="background:linear-gradient(160deg,#c7c4bb,#5a5048 55%,#2f2b28)"></div><h3>Loaders for hire</h3><p>We have a comprehensive range of wheel loaders for hire, and integrated tool carriers available.</p><a href="#">Read More →</a></article>
  </div>
  <a class="btn" href="#">View All <svg viewBox="0 0 16 10"><path d="M0 5h14M10 1l4 4-4 4" stroke="#fff" stroke-width="1.6" fill="none"/></svg></a>
</div></section>

<section class="why"><div class="wrap">
  <div class="visual"><div class="frame"></div><div class="pic" role="img" aria-label="Yellow excavator cut out on white"></div></div>
  <div>
    <h2>Why you should choose us</h2>
    <div class="stats">
      <div class="stat"><svg viewBox="0 0 56 56"><circle cx="28" cy="28" r="22" fill="none" stroke="#1f2577" stroke-width="3"/><path d="M28 14v14l9 6" stroke="#1f2577" stroke-width="3" fill="none"/></svg><div><b>20<sup>+</sup></b><small>Years of Experience</small></div></div>
      <div class="stat"><svg viewBox="0 0 56 56"><rect x="6" y="30" width="30" height="14" fill="none" stroke="#1f2577" stroke-width="3"/><path d="M36 34h12l-4-14H30" stroke="#1f2577" stroke-width="3" fill="none"/><circle cx="14" cy="48" r="4" fill="#1f2577"/><circle cx="30" cy="48" r="4" fill="#1f2577"/></svg><div><b>100<sup>+</sup></b><small>Machines in fleet</small></div></div>
      <div class="stat"><svg viewBox="0 0 56 56"><rect x="8" y="8" width="16" height="16" fill="none" stroke="#1f2577" stroke-width="3"/><rect x="32" y="8" width="16" height="16" fill="none" stroke="#1f2577" stroke-width="3"/><rect x="8" y="32" width="16" height="16" fill="none" stroke="#1f2577" stroke-width="3"/><rect x="32" y="32" width="16" height="16" fill="none" stroke="#1f2577" stroke-width="3"/></svg><div><b>ONE</b><small>of QLD's largest suppliers</small></div></div>
      <div class="stat"><svg viewBox="0 0 56 56"><circle cx="28" cy="28" r="10" fill="none" stroke="#1f2577" stroke-width="3"/><path d="M28 6v8M28 42v8M6 28h8M42 28h8M12 12l6 6M38 38l6 6M44 12l-6 6M12 44l6-6" stroke="#1f2577" stroke-width="3"/></svg><div><b>ONSITE</b><small>Servicing</small></div></div>
      <div class="stat wide"><svg viewBox="0 0 56 56"><path d="M10 44l18-18M28 26l8-14 10 4-8 12z" stroke="#1f2577" stroke-width="3" fill="none"/></svg><div><b>CUSTOM</b><small>Machine attachments</small></div></div>
    </div>
  </div>
</div></section>

<section class="projects"><div class="wrap">
  <div class="head">
    <h2>Latest Project</h2>
    <p>Harlow Brentmere Resources is widely regarded as a civil and commercial earthmover – our systems and processes support larger projects with stringent safety, compliance and productivity expectations.</p>
    <a class="btn" href="#">View All <svg viewBox="0 0 16 10"><path d="M0 5h14M10 1l4 4-4 4" stroke="#fff" stroke-width="1.6" fill="none"/></svg></a>
  </div>
  <div class="pgrid">
    <div class="proj" role="img" aria-label="Earthworks on a road corridor" style="background:linear-gradient(160deg,#a8b9c6,#8d7657)"><div class="cap"><small>Commencement Year – 2019</small><b>Southern Link Corridor Works, Brisbane</b><small>Client – Civil Partners</small></div></div>
    <div class="proj" role="img" aria-label="Excavator beside a river road upgrade" style="background:linear-gradient(160deg,#7f95a8,#b3622d)"><div class="cap"><small>Commencement Year – 2016</small><b>Riverside Drive Upgrade, Brisbane</b><small>Client – Civil Partners</small></div></div>
    <div class="proj" role="img" aria-label="Motorway earthworks with machinery" style="background:linear-gradient(160deg,#c4ccd2,#a65a2c)"><div class="cap"><small>Commencement Year – 2016</small><b>Northern Motorway Stage 2, Brisbane</b><small>Client – Civil Partners</small></div></div>
    <div class="proj" role="img" aria-label="Machines on a rail yard site" style="background:linear-gradient(160deg,#9bb2c6,#7a6a55)"><div class="cap"><small>Commencement Year – 2015</small><b>Millbrook Rail Yard, QLD</b><small>Client – Rail Works Co</small></div></div>
    <div class="proj" role="img" aria-label="Dozer clearing land near a creek" style="background:linear-gradient(160deg,#b2c0cb,#8a6e44)"><div class="cap"><small>Commencement Year – 2014</small><b>Fernvale Creek, QLD</b><small>Client – Regional Roads</small></div></div>
    <div class="proj" role="img" aria-label="Excavators on a gas pad site" style="background:linear-gradient(160deg,#a9b6c0,#c2582a)"><div class="cap"><small>Commencement Year – 2013</small><b>Eastfield Gas Pad</b><small>Client – Energy Civil Group</small></div></div>
  </div>
</div></section>

<section class="contact"><div class="wrap">
  <form class="form">
    <h2>Contact us today for a free quote</h2>
    <label>Name</label><label>Email</label><label>Phone</label><label class="area">Enquire</label>
    <span class="btn">Submit <svg viewBox="0 0 16 10"><path d="M0 5h14M10 1l4 4-4 4" stroke="#fff" stroke-width="1.6" fill="none"/></svg></span>
  </form>
  <div class="visual"><div class="frame"></div><div class="pic" role="img" aria-label="Yellow backhoe loader cut out on white"></div></div>
</div></section>

<section class="partners">
  <h2>Our Partners</h2>
  <div class="logos"><span class="chev" style="background:none;width:auto;height:auto">‹</span><span></span><span></span><span></span><span></span><span></span><span></span><span></span><span class="chev" style="background:none;width:auto;height:auto">›</span></div>
</section>

<footer class="footer"><div class="wrap">
  <div class="cols">
    <div><h4>LOCATION</h4><p>18 Wattle Ridge Rd,<br>Coomera QLD 4209</p></div>
    <div><h4>GET IN TOUCH</h4><p class="phone">1300 462 915</p></div>
    <div><h4>QUICK LINKS</h4><ul><li>Home</li><li>About us</li><li>Plant Hire</li><li>Major Project Snapshot</li><li>Policies</li><li>Jobs</li><li>Contact Us</li></ul></div>
    <div><h4>OTHER LINKS</h4><ul><li>Articulated dump trucks hire</li><li>Dozer hire</li><li>Excavator diggers hire</li><li>Grader hire</li><li>Attachments hire</li></ul></div>
  </div>
</div>
<div class="legal"><div class="wrap"><span>© 2024 HBR Plant Hire. All right reserved</span><span>www.harlowbrentmere.com.au</span></div></div>
</footer>

</body>
</html>
```